A New and modern Business Card for Tarwick Trade Solutions Ltd

New and modern Logo and Business Card Attached is the current logo/business card designCurrently the business is called "Tarwick & Co." or TTS Ltd for short. This is subject to change.This business specialises in Telecoms and Energy. We work with the major networks (QV, K7, etc) and also offer Energy Products saving clients money off their energy bills.These are business to business services.The current design incorporates a Pheonix, indicating rebirth, starting something new.We would like to maintain the Phoenix element but a newer modern style.We love colours in the logo 3 max.The aim of this is to be ultra slick and modern. I envisage Tarwick & Co. on one side of the card with long descriptions on the other side.Side 1:TTS Ltd/Logo?Side 2:TTS Ltd/Logo/Graphic?Brogan & Co.Name:Address:Phone:Email:The design is mostly flexible but must incorporate a Phoenix.For example "Tarwick & Co." with a block phoenix behind the text...up to you.

Industry/Entity Type

Telecommunications

Contact Information for Business Card

Tarwick & Co.
Address:
Name:
Phone:
Email:

Logo Text

Tarwick & Co.

Colors
33a6d7
0792cd
acd037
9bcb3c
f78f20
fece3e

Requirements
Must have
• Phoenix
• 3/4 colours max
• Blue representing Technology (wireless)
• Green for Eco Energy
• Orange for Phoenix
• White business card background
Should not have
• phoenix must not all be red/ orange fire, we are a technology service company and the phoenix colours must represent this. Fire is not representative of our company.

```html
<!DOCTYPE html>
<html lang="en">
<head>
<meta charset="utf-8">
<title>Tarwick &amp; Co. — Business Card</title>
<link rel="stylesheet" href="https://fonts.googleapis.com/css2?family=Bebas+Neue&family=Work+Sans:wght@300;400&display=swap">
<style>
  :root {
    --page: #d9d9d9;
    --card-dark: #4a4b4f;
    --card-light: #ffffff;
    --ink: #3d3d3f;
    --ink-soft: #5a5a5c;
    --blue: #1f3d8f;
    --orange: #f7a040;
    --green: #acd037;
  }
  * { box-sizing: border-box; margin: 0; padding: 0; }
  html, body {
    width: 1200px; height: 930px; overflow: hidden;
    background: var(--page);
    font-family: "Work Sans", Arial, sans-serif;
  }
  .canvas { position: relative; width: 1200px; height: 930px; }

  .card {
    position: absolute;
    width: 560px; height: 340px;
    box-shadow: 0 6px 14px rgba(0,0,0,.25);
  }
  .card--front { left: 70px; top: 100px; background: var(--card-dark); }
  .card--back  { left: 570px; top: 490px; background: var(--card-light); }

  .brand {
    position: absolute;
    display: flex; align-items: center; gap: 14px;
    font-family: "Work Sans", Arial, sans-serif;
    font-weight: 300;
    letter-spacing: 1px;
    line-height: 1;
  }
  .brand__mark { width: 34px; height: 34px; background: var(--orange); }
  .card--front .brand { left: 120px; top: 143px; font-size: 54px; color: #ffffff; }
  .card--back .brand { left: 190px; top: 36px; font-size: 48px; color: var(--ink); }
  .card--back .brand__mark { width: 30px; height: 30px; }

  .person { position: absolute; left: 60px; top: 160px; text-align: right; width: 240px; }
  .person__name {
    font-family: "Bebas Neue", Impact, sans-serif;
    font-size: 44px; color: var(--blue); letter-spacing: 1px; line-height: 1;
  }
  .person__role { font-size: 15px; color: var(--ink-soft); margin-top: 2px; }

  .divider {
    position: absolute; left: 330px; top: 130px;
    width: 2px; height: 82px; background: var(--blue);
  }

  .contact { position: absolute; left: 350px; top: 126px; list-style: none; }
  .contact li {
    display: flex; align-items: center; gap: 10px;
    font-size: 14px; color: var(--ink); height: 22px;
  }
  .contact svg { width: 12px; height: 12px; fill: none; stroke: var(--blue); stroke-width: 1.6; }

  .address {
    position: absolute; left: 0; right: 0; bottom: 40px;
    text-align: center; font-size: 15px; color: var(--ink); letter-spacing: .5px;
  }
</style>
</head>
<body>
<main class="canvas">
  <section class="card card--front" aria-label="Card front">
    <div class="brand"><span class="brand__mark"></span><span class="brand__name">tarwick&amp;co</span></div>
  </section>

  <section class="card card--back" aria-label="Card back">
    <div class="brand"><span class="brand__mark"></span><span class="brand__name">tarwick&amp;co</span></div>

    <div class="person">
      <p class="person__name">Daniel Harker</p>
      <p class="person__role">Director</p>
    </div>

    <div class="divider"></div>

    <ul class="contact">
      <li>
        <svg viewBox="0 0 12 12"><path d="M3 1 L5 3.5 L4 5 Q5.5 7 7 8 L8.5 7 L11 9 L9.5 11 Q4 10 1 2.5 Z"/></svg>
        +612 5550 1842
      </li>
      <li>
        <svg viewBox="0 0 12 12"><rect x="3" y="1" width="6" height="3"/><rect x="1" y="4" width="10" height="5"/><rect x="3" y="8" width="6" height="3"/></svg>
        +612 5550 1843
      </li>
      <li>
        <svg viewBox="0 0 12 12"><rect x="1" y="2.5" width="10" height="7"/><path d="M1 2.5 L6 6.5 L11 2.5"/></svg>
        mail@tarwickco.com.au
      </li>
      <li>
        <svg viewBox="0 0 12 12"><circle cx="6" cy="6" r="5"/><ellipse cx="6" cy="6" rx="2.2" ry="5"/><path d="M1 6 H11"/></svg>
        www.tarwickco.com.au
      </li>
    </ul>

    <p class="address">40-48 Wattle Lane Sydney NSW 2000 Australia</p>
  </section>
</main>
</body>
</html>
```